Landscape design build company door flyer

I would like this flyer to convey a high-level of professionalism for a company that is excellent with communication with their clients as well as a company that does incredible installations

Went on vacation/holiday

```html
<!DOCTYPE html>
<html lang="en">
<head>
<meta charset="utf-8">
<title>Summit Stone Builders – Door Flyer</title>
<link rel="stylesheet" href="https://fonts.googleapis.com/css2?family=Marcellus&family=Montserrat:wght@400;500;700;800&display=swap">
<style>
  :root {
    --yellow: #fdb913;
    --navy: #0d2a3b;
    --navy-deep: #0a1f2b;
    --ink: #0b1715;
    --white: #ffffff;
    --serif: "Marcellus", Georgia, serif;
    --sans: "Montserrat", Arial, sans-serif;
  }
  * { box-sizing: border-box; margin: 0; padding: 0; }
  html, body { width: 1200px; height: 1200px; overflow: hidden; }
  body { background: var(--ink); position: relative; font-family: var(--sans); }

  .flyer {
    position: absolute; left: 40px; top: 204px;
    width: 1093px; height: 773px;
    transform: scale(1.0247); transform-origin: 0 0;
    overflow: hidden;
    background: var(--navy-deep);
  }
  .flyer__art { position: absolute; inset: 0; width: 100%; height: 100%; }

  .brand { position: absolute; left: 60px; top: 66px; width: 260px; text-align: center; color: var(--navy); }
  .brand__dot { width: 46px; height: 46px; border-radius: 50%; background: var(--navy); margin: 0 auto 10px; }
  .brand__name { font-family: var(--serif); font-size: 25px; letter-spacing: .5px; line-height: 1; }
  .brand__tag { font-family: var(--sans); font-size: 11px; font-weight: 500; margin-top: 3px; letter-spacing: .2px; }

  .heading {
    position: absolute; font-family: var(--serif); color: var(--yellow);
    display: flex; align-items: center; gap: 6px; white-space: nowrap;
  }
  .heading__rule { height: 1px; background: var(--yellow); flex: 1; }
  .heading--about { left: 70px; top: 280px; width: 327px; font-size: 24px; }
  .heading--services { left: 70px; top: 578px; width: 350px; font-size: 24px; }
  .heading--zen { left: 64px; top: 493px; font-size: 25px; }

  .about-text {
    position: absolute; left: 65px; top: 317px; width: 335px;
    color: var(--white); font-size: 12.6px; font-weight: 500; line-height: 17.9px;
    text-align: justify;
  }
  .zen-text {
    position: absolute; left: 65px; top: 522px; width: 330px;
    color: var(--white); font-size: 12.6px; font-weight: 500; line-height: 18px;
  }

  .services { position: absolute; left: 69px; top: 618px; list-style: none; color: var(--white); font-size: 16.5px; }
  .services li { position: absolute; display: flex; align-items: center; gap: 9px; white-space: nowrap; }
  .services__icon { width: 19px; height: 19px; background: var(--yellow); position: relative; flex: none; }
  .services__icon::after { content: ""; position: absolute; inset: 4px; border: 1.5px solid var(--navy); }

  .cta { position: absolute; left: 698px; top: 628px; color: var(--white); }
  .cta__label { font-size: 20px; font-weight: 800; color: var(--yellow); }
  .cta__phone { display: flex; align-items: center; gap: 4px; font-size: 34px; font-weight: 800; margin-top: 4px; letter-spacing: .3px; }
  .cta__button { display: flex; margin-top: 10px; height: 32px; width: 290px; font-size: 21px; font-weight: 800; }
  .cta__button-lead { background: var(--yellow); color: var(--white); width: 88px; display: flex; align-items: center; justify-content: center; }
  .cta__button-main { background: var(--white); color: var(--navy); flex: 1; display: flex; align-items: center; justify-content: center; }
</style>
</head>
<body>
<main class="flyer">
  <svg class="flyer__art" viewBox="0 0 1093 773" aria-hidden="false">
    <defs>
      <linearGradient id="scene" x1="0" y1="0" x2="1" y2="1">
        <stop offset="0" stop-color="#1b3a30"/>
        <stop offset=".5" stop-color="#16303a"/>
        <stop offset="1" stop-color="#102430"/>
      </linearGradient>
    </defs>
    <rect width="1093" height="773" fill="url(#scene)" role="img" aria-label="Evening photo of a covered backyard patio with stone columns and lawn"/>
    <rect width="1093" height="773" fill="#0a1f2b" opacity=".45"/>
    <polygon points="168,250 656,0 1093,0 1093,230 620,240 168,250" fill="#0f2d40" opacity=".85"/>
    <polygon points="0,0 656,0 168,250 0,191" fill="#fdb913"/>
    <polygon points="797,0 1093,0 945,85" fill="#fdb913"/>
    <polygon points="532,81 656,0 783,0 589,113" fill="#ffffff"/>

    <g stroke="#ffffff" stroke-width="4">
      <polygon role="img" aria-label="Photo of paver steps leading to a house" points="704,104 788,152.5 788,249.5 704,298 620,249.5 620,152.5" fill="#6d6a64"/>
      <polygon role="img" aria-label="Aerial photo of fenced backyard plots" points="884,104 968,152.5 968,249.5 884,298 800,249.5 800,152.5" fill="#6f6047"/>
      <polygon role="img" aria-label="Photo of a grey paver patio with wooden fence" points="613,264 697,312.5 697,409.5 613,458 529,409.5 529,312.5" fill="#6e6f70"/>
      <polygon role="img" aria-label="Photo of a covered outdoor kitchen pavilion" points="794,264 878,312.5 878,409.5 794,458 710,409.5 710,312.5" fill="#5b4a3c"/>
      <polygon role="img" aria-label="Photo of a terraced garden with curved walkway" points="975,264 1059,312.5 1059,409.5 975,458 891,409.5 891,312.5" fill="#6b7560"/>
      <polygon role="img" aria-label="Photo of a block retaining wall with planting" points="704,421 788,469.5 788,566.5 704,615 620,566.5 620,469.5" fill="#686a5a"/>
      <polygon role="img" aria-label="Photo of a stone wall with a wooden bench" points="884,421 968,469.5 968,566.5 884,615 800,566.5 800,469.5" fill="#7a6a52"/>
    </g>
  </svg>

  <div class="brand">
    <div class="brand__dot"></div>
    <div class="brand__name">SUMMIT STONE BUILDERS</div>
    <div class="brand__tag">OUTDOOR LIVING SPACES</div>
  </div>

  <h2 class="heading heading--about">ABOUT US<span class="heading__rule"></span></h2>
  <p class="about-text">Marcus Hale founded Summit Stone Builders in 2018. The company is a veteran-owned and operated hardscaping and landscaping design operation. Mr. Hale faithfully served the greater Seattle area for more than two decades. Mr. Hale wants to offer these many years of experience to build up each of Seattle’s exterior spaces to be the most beautiful, functional, and sustainable for both businesses and residents.</p>

  <h2 class="heading heading--zen">It’s Time to Discover Your Zen</h2>
  <p class="zen-text">From vision to reality, let us bring your dream outdoor space to life.</p>

  <h2 class="heading heading--services">Our Services<span class="heading__rule"></span></h2>
  <ul class="services">
    <li style="left:0;top:0"><span class="services__icon"></span>Pools</li>
    <li style="left:0;top:33px"><span class="services__icon"></span>Paver Patios</li>
    <li style="left:0;top:64px"><span class="services__icon"></span>Paver Driveways</li>
    <li style="left:0;top:96px"><span class="services__icon"></span>Retaining Walls</li>
    <li style="left:186px;top:-1px"><span class="services__icon"></span>Decks &amp; Railings</li>
    <li style="left:186px;top:33px"><span class="services__icon"></span>Outdoor Lighting</li>
    <li style="left:186px;top:66px"><span class="services__icon"></span>Firepits and Fireplaces</li>
  </ul>

  <div class="cta">
    <div class="cta__label">Call Us Now!</div>
    <div class="cta__phone">
      <svg width="24" height="24" viewBox="0 0 24 24" aria-hidden="true"><path d="M6.6 10.8c1.4 2.8 3.8 5.1 6.6 6.6l2.2-2.2c.3-.3.7-.4 1-.2 1.1.4 2.3.6 3.6.6.6 0 1 .4 1 1V20c0 .6-.4 1-1 1C10.6 21 3 13.4 3 4c0-.6.4-1 1-1h3.5c.6 0 1 .4 1 1 0 1.3.2 2.5.6 3.6.1.3 0 .7-.2 1z" fill="none" stroke="#fff" stroke-width="2"/></svg>
      (206) 555-0148
    </div>
    <div class="cta__button"><span class="cta__button-lead">GET A</span><span class="cta__button-main">FREE ESTIMATE</span></div>
  </div>
</main>
</body>
</html>
```